Business Card for beauty technology startup

Design Glimora Business Card for a Beauty, based on the website identity and colors (https://www.glimora-example.com).
Glimora is a beauty tech startup that gathers helpful product info for beauty lovers and consumers (such as availability on stores, price range and product reviews) for makeup products. The card design must be young, colorful but clean, and very modern.

Target Market(s)

woman, 15-35

Industry/Entity Type

Cosmetics

Contact Information for Business Card

Full Name, address, phone

Font styles to use
Other font styles liked:
• Advent Pro

Colors
e34297
86cfc6
ffffff
5c5c5c
e8e8e8
e667a6
b2b2b2

Requirements
Must have
• One full colored side with a creative design and another with card info
• Use Color palette: #95C5C5 and/or #D38AA5
• Use fonts: Advent Pro
• Use website identity: https://www.glimora-example.com
Nice to have
• If needed extra font: Roboto

```html
<!DOCTYPE html>
<html lang="en">
<head>
<meta charset="utf-8">
<title>Glimora Business Card</title>
<link rel="stylesheet" href="https://fonts.googleapis.com/css2?family=Advent+Pro:wght@300;400;600&family=Open+Sans:wght@400;700&display=swap">
<style>
  :root {
    --backdrop: #e8e8e8;
    --card-dark: #161618;
    --teal: #95c5c5;
    --teal-bright: #86cfc6;
    --pink: #d38aa5;
    --pink-bright: #e34297;
    --pink-soft: #e667a6;
    --white: #ffffff;
    --text: #f2f2f2;
    --grey: #b2b2b2;
  }
  * { box-sizing: border-box; margin: 0; padding: 0; }
  html, body { width: 1200px; height: 864px; overflow: hidden; }
  body {
    background: var(--backdrop);
    font-family: "Open Sans", Arial, sans-serif;
    position: relative;
  }
  .card {
    position: absolute;
    width: 540px;
    height: 309px;
    border-radius: 3px;
    box-shadow: 0 10px 24px rgba(0,0,0,.22);
    overflow: hidden;
  }
  .card-front {
    left: 50px; top: 110px;
    background: linear-gradient(135deg, var(--pink-soft) 0%, var(--pink) 45%, var(--teal) 100%);
  }
  .card-back { left: 610px; top: 430px; background: var(--card-dark); }

  /* front side */
  .front-brand {
    position: absolute;
    left: 0; right: 0; top: 64px;
    display: flex; flex-direction: column; align-items: center;
  }
  .front-mark {
    width: 62px; height: 62px;
    border: 2px solid var(--white);
    border-radius: 50%;
  }
  .front-name {
    margin-top: 12px;
    font-family: "Advent Pro", "Open Sans", sans-serif;
    font-weight: 400;
    font-size: 44px;
    line-height: 1.1;
    letter-spacing: 10px;
    padding-left: 10px;
    color: var(--white);
    text-transform: uppercase;
  }
  .front-url {
    margin-top: 20px;
    font-size: 13px;
    letter-spacing: 5px;
    padding-left: 5px;
    color: var(--white);
  }

  /* back side */
  .back-brand {
    position: absolute;
    right: 30px; top: 46px;
    display: flex; align-items: center; gap: 14px;
  }
  .back-mark {
    width: 46px; height: 46px;
    border: 2px solid var(--pink);
    border-radius: 50%;
  }
  .back-name {
    font-family: "Advent Pro", "Open Sans", sans-serif;
    font-weight: 400;
    font-size: 40px;
    line-height: 1;
    letter-spacing: 7px;
    color: var(--pink);
    text-transform: uppercase;
  }
  .holder {
    position: absolute;
    left: 26px; top: 126px;
    line-height: 17px;
  }
  .holder-name {
    font-weight: 700;
    font-size: 12px;
    color: var(--pink);
    text-transform: uppercase;
  }
  .holder-role {
    font-size: 12px;
    color: var(--text);
    text-transform: uppercase;
  }
  .divider {
    position: absolute;
    left: 200px; right: 26px; top: 166px;
    height: 1px;
    background: var(--teal);
  }
  .contacts {
    position: absolute;
    left: 26px; top: 170px;
    list-style: none;
  }
  .contacts li {
    display: flex; align-items: center; gap: 8px;
    font-size: 12px;
    line-height: 18px;
    color: var(--text);
  }
  .contacts svg { width: 10px; height: 10px; fill: var(--pink); flex: none; }
  .address {
    position: absolute;
    right: 26px; bottom: 24px;
    text-align: right;
    font-style: normal;
    font-size: 13px;
    line-height: 18px;
    color: var(--text);
  }
  .address .web { letter-spacing: 1.5px; color: var(--teal-bright); }
</style>
</head>
<body>
  <section class="card card-front" aria-label="Card front">
    <div class="front-brand">
      <div class="front-mark"></div>
      <div class="front-name">Glimora</div>
      <div class="front-url">www.glimora-example.com</div>
    </div>
  </section>

  <section class="card card-back" aria-label="Card back">
    <div class="back-brand">
      <div class="back-mark"></div>
      <div class="back-name">Glimora</div>
    </div>

    <div class="holder">
      <p class="holder-name">Mara Ellison</p>
      <p class="holder-role">CEO/Founder</p>
    </div>

    <div class="divider"></div>

    <ul class="contacts">
      <li>
        <svg viewBox="0 0 10 10" aria-hidden="true"><path d="M1 3 Q5 0 9 3 L8 4.5 L6.5 3.8 L6.5 3 Q5 2.5 3.5 3 L3.5 3.8 L2 4.5 Z M2 5 H8 V9 H2 Z"/></svg>
        555 214 7730
      </li>
      <li>
        <svg viewBox="0 0 10 10" aria-hidden="true"><path d="M3 0.5 H7 Q7.8 0.5 7.8 1.3 V8.7 Q7.8 9.5 7 9.5 H3 Q2.2 9.5 2.2 8.7 V1.3 Q2.2 0.5 3 0.5 Z M3.2 1.6 V7.6 H6.8 V1.6 Z" fill-rule="evenodd"/></svg>
        555 381 6042
      </li>
      <li>
        <svg viewBox="0 0 10 10" aria-hidden="true"><path d="M3 0.5 H7 V3.5 H3 Z M1 3.5 H9 V8.5 H1 Z M3 6 H7 V9.5 H3 Z"/></svg>
        555 907 2185
      </li>
      <li>
        <svg viewBox="0 0 10 10" aria-hidden="true"><path d="M0.5 2 H9.5 V8 H0.5 Z M0.8 2.3 L5 5.5 L9.2 2.3 L9.2 2.9 L5 6.1 L0.8 2.9 Z" fill-rule="evenodd"/></svg>
        hello@glimora-example.com
      </li>
    </ul>

    <address class="address">
      2281 Larkspur Avenue<br>
      Juneau, Alaska 99801<br>
      <span class="web">www.glimora-example.com</span>
    </address>
  </section>
</body>
</html>
```